Spring Detox sale graphics for social media

You MUST read the Brief in the WORD document and follow the instructions there. I want to create 10 social media graphics (new Instagram size 4:5 (1080 x 1350 pixels) focusing on our Mother’s Day Spring Detox Sale graphics, using any of the pics attached. Use the attached pics, NO RANDOM STOCK PHOTOGRAPHY. For the color scheme of the graphics, they should all be complementary to the product colors or feel like Spring time.

Target Market(s)

primarily women

Requirements
Must have
• the photos and text attached

```html
<!DOCTYPE html>
<html lang="en">
<head>
<meta charset="utf-8">
<title>Mother's Day Spring Detox Sale – Social Set</title>
<link rel="stylesheet" href="https://fonts.googleapis.com/css2?family=Montserrat:wght@600;700;800;900&family=Playfair+Display:wght@700;800&family=Bebas+Neue&family=Great+Vibes&family=Poppins:wght@500;600;700&family=Fredoka:wght@600&display=swap">
<style>
:root{
  --ink:#161616;
  --red-pink:#ec2a55;
  --soft-pink:#f0567a;
  --magenta:#d2378c;
  --teal-green:#2e6b57;
  --olive:#4b6a12;
  --leaf:#7aa21a;
  --white:#ffffff;
  --frame:#1a1a1a;
}
*{box-sizing:border-box;margin:0;padding:0}
html,body{width:744px;height:1200px;overflow:hidden;background:var(--white)}
.board{position:relative;width:744px;height:1200px}
.post{position:absolute;width:219px;height:274px;overflow:hidden}
.col-1{left:24px}.col-2{left:263px}.col-3{left:502px}
.row-1{top:22px}.row-2{top:315px}.row-3{top:610px}.row-4{top:904px}

.bg-spring{background:linear-gradient(180deg,#5ec9e8 0%,#e6f0e2 24%,#f5f39a 50%,#d3e63c 72%,#7db52a 100%)}
.bg-sky{background:linear-gradient(180deg,#6ed6dc 0%,#dff3ea 24%,#f4f2c8 44%,#d7ea7a 64%,#8fbf2e 84%,#4e8a1e 100%)}
.bg-sun{background:radial-gradient(circle at 50% 35%,#fdfbd0 0%,rgba(253,251,208,0) 55%),linear-gradient(180deg,#fbf7b8 0%,#f3f06a 40%,#e6ea4a 60%,#a9c23a 80%,#3d5a14 100%)}

.frame{position:absolute;left:16px;top:15px;width:188px;height:219px;border:2px solid var(--frame)}

.t{position:absolute;left:0;right:0;text-align:center;white-space:nowrap;line-height:1}
.band{position:absolute;display:flex;align-items:center;justify-content:center;white-space:nowrap;line-height:1}

.f-mont{font-family:'Montserrat',sans-serif;font-weight:800}
.f-serif{font-family:'Playfair Display',serif;font-weight:800}
.f-bebas{font-family:'Bebas Neue',sans-serif}
.f-script{font-family:'Great Vibes',cursive}
.f-pop{font-family:'Poppins',sans-serif;font-weight:600}
.f-round{font-family:'Fredoka',sans-serif;font-weight:600}

.photo-products{position:absolute;border-radius:6px;background:linear-gradient(180deg,#ffffff 0%,#f1f1f3 55%,#d9cfe0 80%,#c7a4c4 100%);opacity:.95}
.photo-model{position:absolute;background:linear-gradient(180deg,rgba(40,30,28,.85) 0%,rgba(90,60,50,.75) 22%,#f3f1ee 38%,#ecebe8 62%,#2a2a2a 78%,#1e1e1e 100%);border-radius:40px 40px 0 0}
.photo-lineup{position:absolute;background:linear-gradient(180deg,#ffffff 0%,#f2f2f4 60%,#dedbe3 100%);border-radius:4px}

/* post 1 */
.p1-head{top:28px;font-size:24px;color:var(--ink)}
.p1-band{left:15px;top:56px;width:188px;height:23px;background:var(--leaf);color:var(--white);font-family:'Playfair Display',serif;font-weight:700;font-size:16px}
.p1-num{position:absolute;left:57px;top:86px;font-family:'Montserrat',sans-serif;font-weight:800;font-size:56px;line-height:1;color:var(--red-pink)}
.p1-pct{position:absolute;left:130px;top:90px;font-family:'Montserrat',sans-serif;font-weight:600;font-size:32px;line-height:1;color:var(--red-pink)}
.p1-off{position:absolute;left:131px;top:121px;font-family:'Montserrat',sans-serif;font-weight:600;font-size:14px;line-height:1;color:var(--red-pink)}
.p1-sub{top:137px;font-size:14px;color:var(--ink)}

/* posts 2 & 3 */
.hero-off{top:22px;font-family:'Montserrat',sans-serif;font-weight:900;font-size:43px;color:var(--red-pink);letter-spacing:-1px}
.hero-sub{top:65px;font-family:'Montserrat',sans-serif;font-weight:700;font-size:17px;color:var(--ink)}
.p2-box{position:absolute;left:16px;top:88px;width:91px;height:94px;background:var(--white);border:1.5px solid #8bb030;border-radius:2px;text-align:center;color:var(--red-pink);font-family:'Playfair Display',serif;font-weight:700;line-height:1}
.p2-box span{display:block}
.p2-box .s1{font-size:24px;margin-top:4px}
.p2-box .s2{font-size:26px}
.p2-box .s3{font-size:34px}
.p3-spring{top:84px;font-family:'Playfair Display',serif;font-weight:800;font-size:34px;color:var(--red-pink)}
.p3-detox{top:121px;font-family:'Montserrat',sans-serif;font-weight:800;font-size:25px;color:var(--ink)}

/* row 2 */
.cond-off{top:20px;font-family:'Bebas Neue',sans-serif;font-size:52px;color:var(--soft-pink)}
.p4-script{top:58px;font-family:'Great Vibes',cursive;font-size:46px;color:var(--teal-green)}
.p4-detox{top:106px;font-family:'Bebas Neue',sans-serif;font-size:40px;color:var(--teal-green)}
.p4-band{left:21px;top:145px;width:179px;height:16px;background:var(--soft-pink);color:var(--white);font-family:'Bebas Neue',sans-serif;font-size:16px}
.p5-every{left:20px;right:auto;top:68px;font-family:'Bebas Neue',sans-serif;font-size:28px;color:var(--teal-green);text-align:left}
.p5-band{left:21px;top:95px;width:112px;height:22px;background:var(--soft-pink);color:var(--white);font-family:'Bebas Neue',sans-serif;font-size:20px}
.p5-box{position:absolute;left:21px;top:128px;width:69px;height:84px;background:rgba(255,255,255,.9);border:1.5px solid var(--teal-green);border-radius:2px;text-align:center;line-height:1}
.p5-box .s1{display:block;font-family:'Great Vibes',cursive;font-size:24px;color:var(--teal-green);margin-top:4px}
.p5-box .s2{display:block;font-family:'Bebas Neue',sans-serif;font-size:24px;color:var(--soft-pink)}
.p5-box .s3{display:block;font-family:'Bebas Neue',sans-serif;font-size:30px;color:var(--soft-pink)}
.p6-mom{top:67px;font-family:'Bebas Neue',sans-serif;font-size:34px;color:var(--teal-green)}
.p6-sale{top:95px;font-family:'Great Vibes',cursive;font-size:38px;color:var(--soft-pink)}
.p6-band{left:20px;top:131px;width:179px;height:22px;background:var(--teal-green);color:var(--white);font-family:'Bebas Neue',sans-serif;font-size:21px}

/* rows 3 & 4 */
.p7-num{position:absolute;left:42px;top:28px;font-family:'Poppins',sans-serif;font-weight:700;font-size:80px;line-height:.8;color:var(--magenta)}
.p7-pct{position:absolute;left:139px;top:28px;font-family:'Poppins',sans-serif;font-weight:600;font-size:40px;line-height:1;color:var(--magenta)}
.p7-off{position:absolute;left:139px;top:72px;font-family:'Poppins',sans-serif;font-weight:500;font-size:20px;line-height:1;color:var(--magenta)}
.p7-mom{top:97px;font-family:'Poppins',sans-serif;font-weight:600;font-size:17px;color:var(--olive)}
.p7-sale{top:112px;font-family:'Great Vibes',cursive;font-size:34px;color:var(--olive)}
.p7-band{left:42px;top:146px;width:133px;height:18px;background:var(--magenta);color:var(--white);font-family:'Poppins',sans-serif;font-weight:600;font-size:11px}
.p8-num{position:absolute;left:29px;top:29px;font-family:'Poppins',sans-serif;font-weight:700;font-size:70px;line-height:.8;color:var(--magenta)}
.p8-pct{position:absolute;left:107px;top:29px;font-family:'Poppins',sans-serif;font-weight:600;font-size:34px;line-height:1;color:var(--magenta)}
.p8-off{position:absolute;left:107px;top:65px;font-family:'Poppins',sans-serif;font-weight:500;font-size:17px;line-height:1;color:var(--magenta)}
.p8-box{position:absolute;left:31px;top:85px;width:68px;height:81px;border:1.5px solid var(--frame);border-radius:2px;text-align:center;line-height:1}
.p8-box .s1{display:block;font-family:'Great Vibes',cursive;font-size:24px;color:var(--teal-green);margin-top:3px}
.p8-box .s2{display:block;font-family:'Bebas Neue',sans-serif;font-size:23px;color:var(--magenta)}
.p8-box .s3{display:block;font-family:'Bebas Neue',sans-serif;font-size:29px;color:var(--magenta)}
.p8-line1{left:30px;right:auto;top:174px;font-family:'Bebas Neue',sans-serif;font-size:15px;color:var(--olive);text-align:left}
.p8-line2{left:30px;right:auto;top:188px;font-family:'Bebas Neue',sans-serif;font-size:17px;color:var(--magenta);text-align:left}
.round-off{font-family:'Fredoka',sans-serif;font-weight:600;font-size:52px;color:var(--magenta);letter-spacing:-1px}
.p9-off{top:34px}
.olive-band{left:28px;width:162px;height:22px;background:var(--olive);color:var(--white);font-family:'Bebas Neue',sans-serif;font-size:21px}
.p9-band{top:85px}
.p9-detox{top:113px;font-family:'Bebas Neue',sans-serif;font-size:24px;color:var(--magenta)}
.p9-shine{top:134px;font-family:'Great Vibes',cursive;font-size:26px;color:var(--olive)}
.p10-off{top:34px}
.p10-band{top:83px;left:31px;width:157px}
.p10-spring{top:105px;font-family:'Great Vibes',cursive;font-size:40px;color:var(--magenta)}
.p10-detox{top:146px;font-family:'Bebas Neue',sans-serif;font-size:31px;color:var(--olive)}
.p10-for{left:91px;top:176px;width:39px;height:18px;background:var(--soft-pink);color:var(--white);font-family:'Bebas Neue',sans-serif;font-size:15px}
.p10-body{top:197px;font-family:'Bebas Neue',sans-serif;font-size:33px;color:var(--soft-pink)}
</style>
</head>
<body>
<main class="board">

  <!-- Row 1 -->
  <section class="post col-1 row-1 bg-spring">
    <p class="t f-mont p1-head">MOTHER'S DAY</p>
    <div class="band p1-band">SPRING DETOX SALE</div>
    <span class="p1-num">25</span><span class="p1-pct">%</span><span class="p1-off">OFF</span>
    <p class="t f-mont p1-sub">EVERYTHING!</p>
    <div class="photo-products" style="left:28px;top:158px;width:162px;height:96px" role="img" aria-label="Four supplement bottles from the detox range"></div>
  </section>

  <section class="post col-2 row-1 bg-spring">
    <p class="t hero-off">25%OFF</p>
    <p class="t hero-sub" style="left:16px;text-align:left">MOTHER'S DAY</p>
    <div class="p2-box"><span class="s1">Spring</span><span class="s2">Detox</span><span class="s3">Sale</span></div>
    <div class="photo-model" style="left:118px;top:79px;width:92px;height:195px" role="img" aria-label="Smiling woman in a white knit top presenting the products"></div>
    <div class="photo-lineup" style="left:92px;top:215px;width:127px;height:49px" role="img" aria-label="Row of supplement bottles and skincare tubes"></div>
  </section>

  <section class="post col-3 row-1 bg-spring">
    <p class="t hero-off">25%OFF</p>
    <p class="t hero-sub">ALL SUPPLEMENTS</p>
    <p class="t p3-spring">Spring</p>
    <p class="t p3-detox">DETOX SALE!</p>
    <div class="photo-products" style="left:15px;top:164px;width:192px;height:80px" role="img" aria-label="Four supplement bottles in a row"></div>
  </section>

  <!-- Row 2 -->
  <section class="post col-1 row-2 bg-sky">
    <p class="t cond-off">25%OFF</p>
    <p class="t p4-script">Spring</p>
    <p class="t p4-detox">DETOX SALE</p>
    <div class="band p4-band">SPRING RESET. SUMMER READY</div>
    <div class="photo-products" style="left:18px;top:174px;width:186px;height:77px" role="img" aria-label="Four supplement bottles in a row"></div>
  </section>

  <section class="post col-2 row-2 bg-sky">
    <p class="t cond-off" style="left:20px;text-align:left">25%OFF</p>
    <p class="t p5-every">EVERYTHING</p>
    <div class="band p5-band">MOTHER'S DAY</div>
    <div class="p5-box"><span class="s1">Spring</span><span class="s2">DETOX</span><span class="s3">SALE</span></div>
    <div class="photo-model" style="left:118px;top:86px;width:92px;height:188px" role="img" aria-label="Smiling woman in a white knit top presenting the products"></div>
    <div class="photo-lineup" style="left:92px;top:216px;width:127px;height:50px" role="img" aria-label="Row of supplement bottles and skincare tubes"></div>
  </section>

  <section class="post col-3 row-2 bg-sky">
    <p class="t cond-off">25%OFF</p>
    <p class="t p6-mom">MOTHER'S DAY</p>
    <p class="t p6-sale">Sale</p>
    <div class="band p6-band">FEEL AMAZING AGAIN!</div>
    <div class="photo-products" style="left:22px;top:160px;width:175px;height:100px" role="img" aria-label="Four supplement bottles grouped together"></div>
  </section>

  <!-- Row 3 -->
  <section class="post col-1 row-3 bg-sun">
    <div class="frame"></div>
    <span class="p7-num">25</span><span class="p7-pct">%</span><span class="p7-off">OFF</span>
    <p class="t p7-mom">MOTHER'S DAY</p>
    <p class="t p7-sale">Sale</p>
    <div class="band p7-band">REFRESH YOUR BODY</div>
    <div class="photo-products" style="left:34px;top:167px;width:154px;height:88px" role="img" aria-label="Four supplement bottles grouped together"></div>
  </section>

  <section class="post col-2 row-3 bg-sun">
    <div class="frame"></div>
    <span class="p8-num">25</span><span class="p8-pct">%</span><span class="p8-off">OFF</span>
    <div class="p8-box"><span class="s1">Spring</span><span class="s2">DETOX</span><span class="s3">SALE</span></div>
    <p class="t p8-line1">SPRING CLEANSE.</p>
    <p class="t p8-line2">SUMMER GLOW</p>
    <div class="photo-model" style="left:118px;top:78px;width:92px;height:196px" role="img" aria-label="Smiling woman in a white knit top presenting the products"></div>
    <div class="photo-lineup" style="left:92px;top:216px;width:127px;height:50px" role="img" aria-label="Row of supplement bottles and skincare tubes"></div>
  </section>

  <section class="post col-3 row-3 bg-sun">
    <div class="frame"></div>
    <p class="t round-off p9-off">25%off</p>
    <div class="band olive-band p9-band">MOTHER'S DAY SALE</div>
    <p class="t p9-detox">DETOX THIS SPRING</p>
    <p class="t p9-shine">Shine This Summer</p>
    <div class="photo-products" style="left:15px;top:174px;width:192px;height:82px" role="img" aria-label="Four supplement bottles in a row"></div>
  </section>

  <!-- Row 4 -->
  <section class="post col-1 row-4 bg-sun">
    <div class="frame"></div>
    <p class="t round-off p10-off">25%off</p>
    <div class="band olive-band p10-band">MOTHER'S DAY SALE</div>
    <p class="t p10-spring">Spring</p>
    <p class="t p10-detox">DETOX</p>
    <div class="band p10-for">FOR A</div>
    <p class="t p10-body">SUMMER BODY</p>
  </section>

</main>
</body>
</html>
```